Brookmere Osteopathy flyer

I want a clean clear DL flyer (but also want an A4 poster) promoting a new Osteopathic business in a semi rural area in Tasmania (Australia).
It can have pictures like the examples attached to show people what Osteopathy is (its like Chiropractic and physiotherapy).
I am the sole practioner and am male, so any pictures would be best to be a white male if possible.
I've attached some wording, you can use all, or none of it
I don't have a phone number for the business yet
info@brookmereosteopathy.example
www.brookmereosteopathy.example
Target Market(s)
Australians, from tradies, professionals, babies to retired people
Industry/Entity Type
Health
Look and feel

```html
<!DOCTYPE html>
<html lang="en">
<head>
<meta charset="utf-8">
<title>Brookmere Osteopathy flyer</title>
<link rel="stylesheet" href="https://fonts.googleapis.com/css2?family=Oswald:wght@500&family=Kumbh+Sans:ital,wght@0,500;0,600;1,500&display=swap">
<style>
  :root {
    --backdrop: #c2c2c2;
    --blue-main: #4aaee3;
    --blue-deep: #1f9fe0;
    --blue-light: #80c7eb;
    --blue-shadow: #1593d0;
    --sage: #8fa5a0;
    --orange: #f7913d;
    --white: #ffffff;
    --brand: #1e8fd0;
  }
  * { margin: 0; padding: 0; box-sizing: border-box; }
  html, body {
    width: 819px; height: 1200px; overflow: hidden;
    background: var(--backdrop);
  }
  .flyer {
    position: absolute; left: 36px; top: 40px;
    width: 747px; height: 1120px;
    background: var(--blue-main);
    overflow: hidden;
    color: var(--white);
    font-family: "Kumbh Sans", sans-serif;
  }
  .flyer__shapes { position: absolute; inset: 0; width: 100%; height: 100%; }
  .brand {
    position: absolute; left: 34px; top: 62px; width: 150px;
    text-align: center;
  }
  .brand__dot {
    display: block; width: 26px; height: 26px; margin: 0 auto 10px;
    border-radius: 50%; background: var(--orange);
  }
  .brand__name {
    font-family: "Kumbh Sans", sans-serif; font-weight: 600;
    font-size: 21px; line-height: 1.15; color: var(--brand);
  }
  .headline {
    position: absolute; left: 35px; top: 356px;
    font-family: "Oswald", sans-serif; font-weight: 500;
    font-size: 38px; line-height: 46.5px; letter-spacing: -0.3px;
    text-transform: uppercase;
  }
  .conditions {
    position: absolute; left: 31px; top: 611px; list-style: none;
  }
  .conditions__item {
    display: flex; align-items: center; gap: 9px;
    height: 32.2px; font-size: 18.5px; font-weight: 500;
  }
  .conditions__icon { width: 24px; height: 24px; flex: none; }
  .contact {
    position: absolute; left: 31px; top: 998px; list-style: none;
    font-size: 15.5px; font-weight: 500;
  }
  .contact__item { display: flex; align-items: center; gap: 6px; height: 21.8px; }
  .contact__icon { width: 17px; height: 17px; flex: none; }
  .about {
    position: absolute; right: 30px; top: 974px; width: 270px;
    text-align: right; font-style: italic; font-weight: 500;
    font-size: 17px; line-height: 23.3px;
  }
</style>
</head>
<body>
<main class="flyer">
  <svg class="flyer__shapes" viewBox="0 0 1446 2168" preserveAspectRatio="none" aria-hidden="false">
    <path class="shape-top-band" fill="var(--blue-deep)" d="M0,0 H1100 C700,260 330,470 290,760 L0,900 Z"/>
    <path class="shape-logo-field" fill="var(--white)" d="M0,0 H350 C420,80 470,160 465,250 C458,380 360,470 240,470 C130,470 50,400 0,320 Z"/>
    <path class="shape-photo-ring" fill="var(--blue-light)" d="M880,0 C520,240 285,480 285,770 C285,1150 620,1380 950,1380 C1200,1380 1350,1300 1446,1230 V0 Z"/>
    <path class="shape-spine-top" fill="var(--blue-shadow)" opacity="0.55" role="img" aria-label="Stylised spine decoration" d="M0,1100 C120,1110 260,1120 370,1090 C300,1140 200,1170 80,1170 L0,1160 Z"/>
    <path class="shape-spine-bottom" fill="var(--blue-shadow)" opacity="0.55" role="img" aria-label="Stylised spine decoration" d="M10,1920 C200,1820 500,1830 850,1820 C720,1900 500,1950 250,1930 C150,1925 60,1935 10,1920 Z"/>
    <defs>
      <linearGradient id="photoTone" x1="0" y1="0" x2="1" y2="1">
        <stop offset="0" stop-color="#e3e6e8"/>
        <stop offset="0.5" stop-color="#9fc3cc"/>
        <stop offset="1" stop-color="#d9c9bd"/>
      </linearGradient>
    </defs>
    <path class="shape-photo" fill="url(#photoTone)" role="img" aria-label="Photo: osteopath in scrubs treating the shoulder of a patient lying on a treatment table" d="M1060,0 C600,300 395,500 395,760 C395,1100 700,1335 950,1335 C1150,1335 1300,1240 1446,1150 V0 Z"/>
    <path class="shape-sage" fill="var(--sage)" d="M850,2168 C870,1950 1050,1700 1446,1480 V2168 Z"/>
    <path class="shape-orange" fill="var(--orange)" d="M790,2168 C740,1950 860,1800 1100,1720 C1250,1670 1360,1620 1446,1600 V2168 Z"/>
  </svg>

  <div class="brand">
    <span class="brand__dot"></span>
    <p class="brand__name">Brookmere Osteopathy</p>
  </div>

  <h1 class="headline">Common<br>reasons<br>people<br>visit an<br>osteopath</h1>

  <ul class="conditions">
    <li class="conditions__item"><svg class="conditions__icon" viewBox="0 0 24 24"><circle cx="12" cy="12" r="10" fill="none" stroke="#fff" stroke-width="1.6"/><circle cx="12" cy="12" r="6.5" fill="none" stroke="#fff" stroke-width="1.4"/><path d="M12 8.5 L15.5 12 L12 15.5 L8.5 12 Z" fill="#fff"/></svg>Back / neck pain</li>
    <li class="conditions__item"><svg class="conditions__icon" viewBox="0 0 24 24"><circle cx="12" cy="12" r="10" fill="none" stroke="#fff" stroke-width="1.6"/><circle cx="12" cy="12" r="6.5" fill="none" stroke="#fff" stroke-width="1.4"/><path d="M12 8.5 L15.5 12 L12 15.5 L8.5 12 Z" fill="#fff"/></svg>Headaches / migraines</li>
    <li class="conditions__item"><svg class="conditions__icon" viewBox="0 0 24 24"><circle cx="12" cy="12" r="10" fill="none" stroke="#fff" stroke-width="1.6"/><circle cx="12" cy="12" r="6.5" fill="none" stroke="#fff" stroke-width="1.4"/><path d="M12 8.5 L15.5 12 L12 15.5 L8.5 12 Z" fill="#fff"/></svg>Joint and muscle pain</li>
    <li class="conditions__item"><svg class="conditions__icon" viewBox="0 0 24 24"><circle cx="12" cy="12" r="10" fill="none" stroke="#fff" stroke-width="1.6"/><circle cx="12" cy="12" r="6.5" fill="none" stroke="#fff" stroke-width="1.4"/><path d="M12 8.5 L15.5 12 L12 15.5 L8.5 12 Z" fill="#fff"/></svg>Pregnancy-related discomfort</li>
    <li class="conditions__item"><svg class="conditions__icon" viewBox="0 0 24 24"><circle cx="12" cy="12" r="10" fill="none" stroke="#fff" stroke-width="1.6"/><circle cx="12" cy="12" r="6.5" fill="none" stroke="#fff" stroke-width="1.4"/><path d="M12 8.5 L15.5 12 L12 15.5 L8.5 12 Z" fill="#fff"/></svg>Disc related issues</li>
    <li class="conditions__item"><svg class="conditions__icon" viewBox="0 0 24 24"><circle cx="12" cy="12" r="10" fill="none" stroke="#fff" stroke-width="1.6"/><circle cx="12" cy="12" r="6.5" fill="none" stroke="#fff" stroke-width="1.4"/><path d="M12 8.5 L15.5 12 L12 15.5 L8.5 12 Z" fill="#fff"/></svg>Sciatica</li>
    <li class="conditions__item"><svg class="conditions__icon" viewBox="0 0 24 24"><circle cx="12" cy="12" r="10" fill="none" stroke="#fff" stroke-width="1.6"/><circle cx="12" cy="12" r="6.5" fill="none" stroke="#fff" stroke-width="1.4"/><path d="M12 8.5 L15.5 12 L12 15.5 L8.5 12 Z" fill="#fff"/></svg>Plantar fasciitis</li>
    <li class="conditions__item"><svg class="conditions__icon" viewBox="0 0 24 24"><circle cx="12" cy="12" r="10" fill="none" stroke="#fff" stroke-width="1.6"/><circle cx="12" cy="12" r="6.5" fill="none" stroke="#fff" stroke-width="1.4"/><path d="M12 8.5 L15.5 12 L12 15.5 L8.5 12 Z" fill="#fff"/></svg>Tendonitis / Bursitis</li>
    <li class="conditions__item"><svg class="conditions__icon" viewBox="0 0 24 24"><circle cx="12" cy="12" r="10" fill="none" stroke="#fff" stroke-width="1.6"/><circle cx="12" cy="12" r="6.5" fill="none" stroke="#fff" stroke-width="1.4"/><path d="M12 8.5 L15.5 12 L12 15.5 L8.5 12 Z" fill="#fff"/></svg>Adhesive capsulitis (frozen shoulder)</li>
    <li class="conditions__item"><svg class="conditions__icon" viewBox="0 0 24 24"><circle cx="12" cy="12" r="10" fill="none" stroke="#fff" stroke-width="1.6"/><circle cx="12" cy="12" r="6.5" fill="none" stroke="#fff" stroke-width="1.4"/><path d="M12 8.5 L15.5 12 L12 15.5 L8.5 12 Z" fill="#fff"/></svg>Tennis / Golfers elbow</li>
  </ul>

  <ul class="contact">
    <li class="contact__item"><svg class="contact__icon" viewBox="0 0 20 20"><circle cx="10" cy="10" r="9" fill="none" stroke="#fff" stroke-width="1.4"/><path d="M10 15 C7 11.5 6.5 10 6.5 8.5 A3.5 3.5 0 0 1 13.5 8.5 C13.5 10 13 11.5 10 15 Z" fill="none" stroke="#fff" stroke-width="1.4"/><circle cx="10" cy="8.5" r="1.2" fill="#fff"/></svg>24 Mill Lane, Brookmere</li>
    <li class="contact__item"><svg class="contact__icon" viewBox="0 0 20 20"><circle cx="10" cy="10" r="9" fill="none" stroke="#fff" stroke-width="1.4"/><path d="M7 5.5 L8.8 5.5 L9.5 8 L8.4 8.9 C9 10.3 9.8 11.1 11.1 11.6 L12 10.5 L14.5 11.2 L14.5 13 C10 13.5 6.5 10 7 5.5 Z" fill="#fff"/></svg>&nbsp;xxxx xxx xxx</li>
    <li class="contact__item"><svg class="contact__icon" viewBox="0 0 20 20"><circle cx="10" cy="10" r="9" fill="none" stroke="#fff" stroke-width="1.4"/><circle cx="10" cy="10" r="5" fill="none" stroke="#fff" stroke-width="1.1"/><path d="M5 10 H15 M10 5 C8 7.5 8 12.5 10 15 M10 5 C12 7.5 12 12.5 10 15" fill="none" stroke="#fff" stroke-width="1"/></svg>www.brookmereosteopathy.example</li>
    <li class="contact__item"><svg class="contact__icon" viewBox="0 0 20 20"><circle cx="10" cy="10" r="9" fill="none" stroke="#fff" stroke-width="1.4"/><rect x="5.5" y="7" width="9" height="6.5" fill="none" stroke="#fff" stroke-width="1.2"/><path d="M5.5 7 L10 10.8 L14.5 7" fill="none" stroke="#fff" stroke-width="1.2"/></svg>info@brookmereosteopathy.example</li>
  </ul>

  <p class="about">Osteopaths use a combination of joint manipulation, targeted deep tissue massage and stretching to improve function relieve pain and support the body’s ability to heal itself.</p>
</main>
</body>
</html>
```